Veldmark Supplies Business Card

Professional business card that stand out to our potential customers. Front and back with clean modern design

Industry/Entity Type

Oil and gas

Contact Information for Business Card

Name, address, website , office phone and cell number

Requirements
Must have
• Editable files for each employee

```html
<!DOCTYPE html>
<html lang="en">
<head>
<meta charset="utf-8">
<title>Veldmark Supplies Business Card</title>
<link href="https://fonts.googleapis.com/css2?family=Lato:wght@400;700;900&display=swap" rel="stylesheet">
<style>
  :root {
    --stage: #151515;
    --card: #1f1f1f;
    --red: #ff0a0a;
    --cyan: #00b1d2;
    --text: #d4d4d4;
  }
  * { box-sizing: border-box; margin: 0; padding: 0; }
  html, body { width: 1200px; height: 801px; overflow: hidden; }
  body {
    background: radial-gradient(ellipse at 50% 40%, #3a3a3a 0%, var(--stage) 70%);
    font-family: "Lato", sans-serif;
    position: relative;
  }
  .card {
    position: absolute;
    top: 252px;
    width: 520px;
    height: 297px;
    background: var(--card);
    border-radius: 14px;
    overflow: hidden;
    box-shadow: 0 18px 40px rgba(0,0,0,.55);
  }
  .card--front { left: 50px; }
  .card--back { left: 630px; }
  .band { position: absolute; left: 0; right: 0; height: 6px; display: flex; }
  .band--top { top: 0; }
  .band--bottom { bottom: 0; }
  .band span { height: 100%; }
  .band .cyan { background: var(--cyan); }
  .band .red { background: var(--red); }
  .band .gap { width: 4px; background: var(--card); }

  .front-brand {
    position: absolute; inset: 0;
    display: flex; flex-direction: column; align-items: center; justify-content: center;
    gap: 14px;
  }
  .brand-mark { width: 26px; height: 26px; background: var(--red); }
  .brand-name {
    font-weight: 900; font-size: 30px; letter-spacing: 2px;
    color: var(--red); text-transform: uppercase;
  }

  .back-brand {
    position: absolute; left: 0; top: 0; width: 250px; height: 100%;
    display: flex; flex-direction: column; align-items: center; justify-content: center; gap: 12px;
  }
  .back-brand .brand-name { font-size: 22px; letter-spacing: 1px; text-align: center; line-height: 1.15; }
  .divider {
    position: absolute; left: 250px; top: 60px; width: 1px; height: 177px; background: var(--red);
  }
  .details { position: absolute; left: 276px; top: 50px; right: 20px; }
  .person-name { font-weight: 900; font-size: 24px; color: var(--red); letter-spacing: .5px; }
  .person-role { font-size: 14px; color: var(--cyan); margin-top: 2px; }
  .contact { list-style: none; margin-top: 14px; }
  .contact li {
    display: flex; align-items: flex-start; gap: 10px;
    font-size: 12px; color: var(--text); line-height: 1.4; margin-bottom: 3px;
  }
  .contact svg { flex: none; width: 12px; height: 12px; margin-top: 2px; fill: var(--cyan); }
</style>
</head>
<body>

<section class="card card--front" aria-label="Card front">
  <div class="band band--top"><span class="cyan" style="width:30%"></span><span class="gap"></span><span class="red" style="flex:1"></span></div>
  <div class="front-brand">
    <span class="brand-mark"></span>
    <span class="brand-name">Veldmark Supplies</span>
  </div>
  <div class="band band--bottom"><span class="red" style="width:70%"></span><span class="gap"></span><span class="cyan" style="flex:1"></span></div>
</section>

<section class="card card--back" aria-label="Card back">
  <div class="band band--top"><span class="cyan" style="width:30%"></span><span class="gap"></span><span class="red" style="flex:1"></span></div>
  <div class="back-brand">
    <span class="brand-mark"></span>
    <span class="brand-name">Veldmark<br>Supplies</span>
  </div>
  <div class="divider"></div>
  <div class="details">
    <h1 class="person-name">DANIEL HARGROVE</h1>
    <p class="person-role">Founder &amp; CEO</p>
    <ul class="contact">
      <li><svg viewBox="0 0 12 12"><path d="M6 0a4 4 0 0 0-4 4c0 3 4 8 4 8s4-5 4-8a4 4 0 0 0-4-4zm0 5.5A1.5 1.5 0 1 1 6 2.5a1.5 1.5 0 0 1 0 3z"/></svg><span>423 Street Address Here, City<br>State &amp; Country, ZIP Code</span></li>
      <li><svg viewBox="0 0 12 12"><path d="M2.5 0.5l2 2.5-1 1.3a7 7 0 0 0 4.2 4.2l1.3-1 2.5 2-1.2 2A10 10 0 0 1 .5 1.7z"/></svg><span>(555) 210-4471</span></li>
      <li><svg viewBox="0 0 12 12"><path d="M3 0h6a1 1 0 0 1 1 1v10a1 1 0 0 1-1 1H3a1 1 0 0 1-1-1V1a1 1 0 0 1 1-1zm.5 1.5v7.5h5V1.5z"/></svg><span>(555) 210-4472</span></li>
      <li><svg viewBox="0 0 12 12"><path d="M3 0h6v3H3zM1 4h10v5H9v3H3V9H1zm3 4v3h4V8z"/></svg><span>(555) 210-4473</span></li>
      <li><svg viewBox="0 0 12 12"><path d="M0 2h12v8H0zm1 1l5 4 5-4z"/></svg><span>info@veldmarksupplies.com</span></li>
      <li><svg viewBox="0 0 12 12"><path d="M6 0a6 6 0 1 0 0 12A6 6 0 0 0 6 0zm0 1.2a4.8 4.8 0 0 1 4.8 4.8H1.2A4.8 4.8 0 0 1 6 1.2zm0 9.6A4.8 4.8 0 0 1 1.3 7h9.4A4.8 4.8 0 0 1 6 10.8z"/></svg><span>veldmarksupplies.com</span></li>
    </ul>
  </div>
  <div class="band band--bottom"><span class="red" style="width:70%"></span><span class="gap"></span><span class="cyan" style="flex:1"></span></div>
</section>

</body>
</html>
```